Short fill E liquid label UK. 100ml Nicotine free

Short Fill e liquid label (UK). The BRAND name is "Lumora" (Logo uploaded).Looking to release a new range under the Lumora name. The new range will be called "Glitch". A range of Liquids mixed together. Needs to look cool, stand out and funky but not too crazy. The range will have 10 different flavours so will need these all done, a simple flavour name towards bottom of label will do for this or a different colour for each.Any warnings ( requirements by law) etc and company address/details etc need to have a place on the labels. Basically need to be E liquid compliant label but all are nicotine free so not so many law requirements.Label Size will be 120mm( wide)x 60mm(high), bottle diameter is 41mm .

The 10 flavour names are as follows so will need appropriate colours for each flavour:
Frostbite ( a menthol and custard mix )
Fruit loop ( a mixed fruit mix )
Smooth custard ( custard based mix )
Strawberry Shake ( Strawberry milkshake mix )
Cookie Jar ( a cookie based mix )
Black ice ( a liquorice and menthol mix )
Madagascan breeze ( Mainly vanilla based mix )
Choc shake ( chocolate milkshake )
nutter ( a peanut butter and banana mix )
Cool currant ( blackcurrant and menthol mix )

Requirements
Must have
• The info and warnings that need to be on the bottle are as follows:
• signs that need to be on bottle:
• 18+ sign
• Caution sign (!)
• United kingdom flag with" made in the united kingdom written underneath"
• text that needs to be on the bottle:
• Nicotine free eliquid. (in bold lettering )
• Keep out of the reach of children. Always
• read the label before use.
• If swallowed consult a doctor if feeling unwell . In case of contact with eyes consult a doctor.
• Dispose of in a responsible manner.
• Store in a dark place at room temperature.
• Ingredients:
• Vegetable glycerin, Propylene glycol, Flavourings.
• PG/VG ratio 70/30 %

```html
<!DOCTYPE html>
<html lang="en">
<head>
<meta charset="utf-8">
<title>Lumora Glitch – Frostbite label</title>
<link rel="stylesheet" href="https://fonts.googleapis.com/css2?family=Source+Sans+3:ital,wght@0,400;0,600;0,700;1,600&family=Montserrat:wght@700&display=swap">
<style>
  :root {
    --page: #f2f2f2;
    --label-dark: #141414;
    --label-mid: #2e2e2e;
    --ink: #ffffff;
    --mint: #7fcfae;
    --mint-deep: #2f8f6a;
    --box: #ffffff;
    --box-ink: #111111;
  }
  * { margin: 0; padding: 0; box-sizing: border-box; }
  html, body { width: 849px; height: 1200px; overflow: hidden; background: var(--page); }
  body { position: relative; font-family: "Source Sans 3", sans-serif; color: var(--ink); }

  .label {
    position: absolute; left: 54px; top: 415px; width: 740px; height: 370px;
    background: linear-gradient(160deg, var(--label-dark) 0%, var(--label-mid) 55%, var(--label-dark) 100%);
    overflow: hidden;
  }
  .block { position: absolute; text-align: center; }

  /* safety column */
  .safety { left: 30px; top: 34px; width: 188px; font-size: 13px; line-height: 1.2; }
  .safety .lead { font-size: 14.5px; font-weight: 600; margin-bottom: 12px; }
  .safety p { margin-bottom: 16px; }
  .batch-box {
    position: absolute; left: 31px; top: 238px; width: 187px; height: 35px;
    background: var(--box); color: var(--box-ink); font-size: 9.5px; font-style: italic; font-weight: 600;
    padding: 4px 7px; line-height: 1.3;
  }
  .flag { position: absolute; left: 31px; top: 288px; width: 79px; height: 46px; }
  .origin { position: absolute; left: 120px; top: 297px; width: 100px; font-size: 13px; line-height: 1.2; text-align: center; }

  /* brand column */
  .brand-name {
    left: 300px; top: 36px; width: 144px;
    font-weight: 700; font-size: 26px; color: var(--mint);
  }
  .range-name {
    left: 240px; top: 150px; width: 260px;
    font-weight: 700; font-size: 76px; line-height: 1; letter-spacing: 1px;
  }
  .range-sub {
    left: 240px; top: 246px; width: 260px;
    font-family: "Montserrat", sans-serif; font-size: 10.5px; letter-spacing: 2.6px;
  }
  .flavour-art {
    position: absolute; left: 344px; top: 266px; width: 54px; height: 32px; border-radius: 50%;
    background: radial-gradient(circle, var(--mint) 0%, var(--mint-deep) 100%);
  }
  .flavour-name {
    left: 270px; top: 304px; width: 200px;
    font-weight: 700; font-size: 28px; letter-spacing: 1px; line-height: 1.1;
  }

  /* info column */
  .info { left: 508px; top: 36px; width: 220px; font-size: 13px; line-height: 1.2; }
  .info .head { font-size: 14.5px; font-weight: 600; margin-bottom: 12px; }
  .info .nicotine { font-size: 15px; font-weight: 700; margin: 16px 0 14px; }
  .info .children { font-size: 11.5px; }
  .warnings { position: absolute; left: 564px; top: 206px; display: flex; gap: 12px; align-items: center; }
  .age-badge {
    width: 48px; height: 48px; border-radius: 50%; background: var(--ink); color: var(--box-ink);
    display: flex; align-items: center; justify-content: center; font-weight: 700; font-size: 21px;
  }
  .barcode-area {
    position: absolute; left: 532px; top: 272px; width: 171px; height: 62px;
    background: var(--box); color: var(--box-ink); font-size: 22px;
    display: flex; align-items: center; justify-content: center;
  }
</style>
</head>
<body>
  <main class="label">
    <section class="block safety">
      <p class="lead">Read the label before use.</p>
      <p>If swallowed consult a doctor if feeling unwell . In case of contact with eyes consult a doctor.</p>
      <p>Dispose of in a responsible manner.</p>
      <p>Store in a dark place at room temperature.</p>
    </section>
    <div class="batch-box">Best Before:<br>Batch Number:</div>
    <svg class="flag" viewBox="0 0 60 36" role="img" aria-label="United Kingdom flag">
      <rect width="60" height="36" fill="#1f3f8f"/>
      <path d="M0 0 L60 36 M60 0 L0 36" stroke="#fff" stroke-width="7"/>
      <path d="M0 0 L60 36 M60 0 L0 36" stroke="#d0202e" stroke-width="2.4"/>
      <path d="M30 0 V36 M0 18 H60" stroke="#fff" stroke-width="11"/>
      <path d="M30 0 V36 M0 18 H60" stroke="#d0202e" stroke-width="6.5"/>
    </svg>
    <p class="origin">Made in the<br>United Kingdom</p>

    <div class="block brand-name">Lumora</div>
    <h1 class="block range-name">GLITCH</h1>
    <p class="block range-sub">E-CIGARETTES &amp; LIQUID</p>
    <div class="flavour-art" role="img" aria-label="Mint leaf illustration"></div>
    <h2 class="block flavour-name">FROSTBITE</h2>

    <section class="block info">
      <p class="head">ingredients:</p>
      <p>Vegetable glycerin, Propylene glycol,<br>Flavourings.<br>PG/VG ratio 70/30 %</p>
      <p class="nicotine">Nicotine free eliquid.</p>
      <p class="children">Keep out of the reach of children.<br>Always</p>
    </section>
    <div class="warnings">
      <div class="age-badge">18+</div>
      <svg width="52" height="46" viewBox="0 0 52 46" role="img" aria-label="Caution sign">
        <path d="M26 3 L49 43 H3 Z" fill="none" stroke="#fff" stroke-width="3" stroke-linejoin="round"/>
        <rect x="24.3" y="15" width="3.4" height="16" fill="#fff"/>
        <circle cx="26" cy="36.5" r="2.2" fill="#fff"/>
      </svg>
    </div>
    <div class="barcode-area">bar code</div>
  </main>
</body>
</html>
```